Dietitian needs awesome business card

I need a contemporary design that's eye catching but professional.
My card is to given to doctors, specialists and patients alike.
I manage patients with chronic diseases
I have uploaded my logo and current business card, I would also like the other Certified Clinical Nutritionist logo incorporated into the design

Target Market(s)

Doctors, specialists and patients

Industry/Entity Type

Healthcare

Contact Information for Business Card

www.brightfieldnutrition.com.au
Ph: 0427 561 903
Fax: 6457 2183
email: marcus.k.diet@fernmail.com
Space on the back of the card with: Appointment date, Appointment time and appointment location

Font styles to use
Serif

Colors
fbee3e
876aae
ffc214

Requirements
Must have
• My Logo
• Certified Clinical Nutritionist Logo
• My 4 locations - Pinebrook Medical Centre, North Corrin Health, Hollis Medical, Ashcombe Doctors Surgery
Nice to have
• I like the colours in my current business card

```html
<!DOCTYPE html>
<html lang="en">
<head>
<meta charset="utf-8">
<title>Brightfield Nutrition – Business Card</title>
<link rel="stylesheet" href="https://fonts.googleapis.com/css2?family=Roboto:wght@400;500;700&display=swap">
<style>
  :root {
    --stage: #2e2e30;
    --card: #ffffff;
    --navy: #1b2483;
    --blue-deep: #17208a;
    --blue-mid: #1a7fc4;
    --green: #8cc63f;
    --orange: #f07a22;
    --rule: #c9cdd3;
    --muted: #4a4a4a;
  }
  * { box-sizing: border-box; margin: 0; padding: 0; }
  html, body { width: 1200px; height: 987px; overflow: hidden; }
  body {
    background: var(--stage);
    font-family: "Roboto", Arial, sans-serif;
    position: relative;
  }
  .card {
    position: absolute;
    left: 293px;
    width: 615px;
    height: 351px;
    background: var(--card);
    border-radius: 22px;
    overflow: hidden;
  }
  .card--front { top: 128px; }
  .card--back { top: 507px; }

  /* front */
  .band { position: absolute; inset: 0; }
  .brand {
    position: absolute; left: 50px; top: 62px;
    display: flex; align-items: center; gap: 12px;
  }
  .brand__dot { width: 58px; height: 58px; border-radius: 50%; background: var(--green); }
  .brand__name { font-size: 30px; font-weight: 400; color: var(--navy); }
  .person { position: absolute; left: 52px; top: 166px; }
  .person__name { font-size: 23px; font-weight: 500; color: var(--navy); }
  .person__role { font-size: 16.5px; color: var(--orange); margin-top: 6px; }
  .person__extra { font-size: 16.5px; color: var(--green); margin-top: 3px; }
  .contact {
    position: absolute; right: 27px; top: 227px;
    list-style: none; text-align: right;
  }
  .contact li {
    display: flex; justify-content: flex-end; align-items: center; gap: 12px;
    font-size: 16px; color: #fff; height: 24px;
  }
  .contact svg { width: 15px; height: 15px; fill: #fff; flex: none; }

  /* back */
  .back-photo {
    position: absolute; inset: 0;
    background: radial-gradient(ellipse at 45% 35%, #e4ece0 0%, #f1f4ef 45%, #fbfcfb 80%);
  }
  .appt { position: absolute; inset: 0; padding: 0 42px; }
  .appt__title {
    text-align: center; margin-top: 28px;
    font-size: 20px; font-weight: 500; color: var(--navy);
  }
  .appt__lines { margin-top: 18px; }
  .appt__lines span { display: block; height: 1px; background: var(--rule); margin-bottom: 35px; }
  .appt__when {
    display: flex; align-items: baseline; gap: 8px;
    font-size: 16.5px; color: var(--navy); margin-top: -3px;
  }
  .dots { border-bottom: 2px dotted var(--navy); height: 1px; }
  .ampm { font-size: 13px; }
  .locations {
    list-style: none; display: grid; grid-template-columns: 306px 1fr;
    row-gap: 6px; margin-top: 20px;
  }
  .locations li { display: flex; align-items: center; gap: 6px; font-size: 16px; color: var(--muted); }
  .box { width: 12px; height: 12px; border: 1.5px solid var(--navy); flex: none; }
</style>
</head>
<body>

<section class="card card--front">
  <svg class="band" viewBox="0 0 615 351" preserveAspectRatio="none" aria-hidden="true">
    <defs>
      <linearGradient id="bandFill" x1="0" y1="1" x2="1" y2="0">
        <stop offset="0" stop-color="#1a7fc4"/>
        <stop offset="1" stop-color="#17208a"/>
      </linearGradient>
    </defs>
    <path d="M0,330 C200,330 340,190 615,160 L615,351 L0,351 Z" fill="url(#bandFill)"/>
  </svg>

  <div class="brand">
    <span class="brand__dot"></span>
    <span class="brand__name">Brightfield Nutrition</span>
  </div>

  <div class="person">
    <h1 class="person__name">Marcus Kellaway</h1>
    <p class="person__role">Certified Clinical Nutritionist</p>
    <p class="person__extra">Nutritionist &amp; Chef</p>
  </div>

  <ul class="contact">
    <li>0427 561 903
      <svg viewBox="0 0 24 24"><path d="M6.6 10.8a15 15 0 0 0 6.6 6.6l2.2-2.2c.3-.3.7-.4 1-.2 1.1.4 2.3.6 3.6.6.6 0 1 .4 1 1V20c0 .6-.4 1-1 1A17 17 0 0 1 3 4c0-.6.4-1 1-1h3.5c.6 0 1 .4 1 1 0 1.3.2 2.5.6 3.6.1.3 0 .7-.2 1z"/></svg></li>
    <li>6457 2183
      <svg viewBox="0 0 24 24"><path d="M6 2h9l3 3v4H6zM3 10h18v8h-3v4H6v-4H3zm5 6v4h8v-4z"/></svg></li>
    <li>marcus.k.diet@fernmail.com
      <svg viewBox="0 0 24 24"><path d="M2 5h20v14H2zm2 2v.5l8 5 8-5V7z"/></svg></li>
    <li>brightfieldnutrition.com.au
      <svg viewBox="0 0 24 24"><circle cx="12" cy="12" r="9" fill="none" stroke="#fff" stroke-width="2"/><path d="M3 12h18M12 3v18" stroke="#fff" stroke-width="1.6"/></svg></li>
  </ul>
</section>

<section class="card card--back">
  <div class="back-photo" role="img" aria-label="Soft faded photograph of fresh vegetables and herbs"></div>
  <div class="appt">
    <h2 class="appt__title">YOUR APPOINTMENT</h2>
    <div class="appt__lines"><span></span><span></span><span></span><span></span></div>
    <div class="appt__when">
      <span>Date :</span><span class="dots" style="width:215px"></span>
      <span>Time :</span><span class="dots" style="width:135px"></span>
      <span class="ampm">AM/PM</span>
    </div>
    <ul class="locations">
      <li><span class="box"></span>Pinebrook Medical Centre</li>
      <li><span class="box"></span>Hollis Medical</li>
      <li><span class="box"></span>North Corrin Health</li>
      <li><span class="box"></span>Ashcombe Doctors Surgery</li>
    </ul>
  </div>
</section>

</body>
</html>
```